KTWG application splash screen

We need a 1024x768 image for use as an application splash screen.
The image will be displayed full screen on an 10 inch industrial PC 1024x768 screen while our application is launching. The image should convey that the application is "Waiting for connection to Wi-Fi access point..." and include a graphic of the industrial PC connected to the access point via an Ethernet cable. A list of troubleshooting steps should be included at the bottom of the image. The troubleshooting steps should not be the main focus of the image and should be shown in a smaller font (but still readable at 1024x768 displayed on a 10 inch screen).
I will include a mock up of the general idea of what we are looking for as well as image files for the industrial PC, a screenshot of our application to show on the PC's screen and the AP.
For general look and feel and a sense of corporate branding please review our website https://marrowgatesoilworks.example/. The splash screen should reflect corporate branding.
Target Market(s)
Users of our application
Industry/Entity Type
Agriculture
Look and feel

```html
<!DOCTYPE html>
<html lang="en">
<head>
<meta charset="utf-8">
<title>KTWG – Waiting for Wi-Fi access point</title>
<link href="https://fonts.googleapis.com/css2?family=Poppins:wght@400;500;700&display=swap" rel="stylesheet">
<style>
  :root {
    --page-bg: #ececec;
    --green-light: #62a112;
    --green-mid: #4f8c08;
    --green-dark: #3b7204;
    --text: #ffffff;
    --device-dark: #2b2b2b;
    --screen-tone: #dfe7dc;
    --ap-white: #eef0ee;
    --cable: #1c1c1c;
  }
  * { box-sizing: border-box; margin: 0; padding: 0; }
  html, body {
    width: 1200px; height: 1103px; overflow: hidden;
    background: var(--page-bg);
    font-family: "Poppins", sans-serif;
  }
  .splash {
    position: absolute; left: 0; top: 101px;
    width: 1200px; height: 900px;
    background: radial-gradient(ellipse at 45% 45%, var(--green-light) 0%, var(--green-mid) 55%, var(--green-dark) 100%);
    color: var(--text);
    overflow: hidden;
  }
  .status-icon { position: absolute; left: 566px; top: 44px; width: 98px; height: 90px; }
  .headline {
    position: absolute; left: 0; top: 152px; width: 1200px;
    text-align: center; font-weight: 700; font-size: 44px; line-height: 55px;
    letter-spacing: -0.4px;
  }
  .device {
    position: absolute; left: 124px; top: 303px; width: 339px; height: 268px;
    border-radius: 18px;
    background: linear-gradient(160deg, #3a3a3a, var(--device-dark));
    box-shadow: 0 6px 14px rgba(0,0,0,0.25);
  }
  .device-screen {
    position: absolute; left: 33px; top: 23px; width: 274px; height: 206px;
    background: linear-gradient(180deg, #f4f6f2, var(--screen-tone));
  }
  .cable { position: absolute; left: 0; top: 0; width: 1200px; height: 900px; }
  .access-point {
    position: absolute; left: 1042px; top: 296px; width: 30px; height: 224px;
    border-radius: 6px;
    background: linear-gradient(90deg, #d6d9d6, var(--ap-white) 45%, #cfd3cf);
  }
  .label { position: absolute; font-weight: 700; font-size: 19px; line-height: 23px; text-transform: uppercase; white-space: nowrap; }
  .label-computer { left: 124px; width: 339px; top: 588px; text-align: center; }
  .label-cable { left: 505px; top: 555px; }
  .label-ap { left: 765px; top: 443px; }
  .label-ap .model { display: block; font-weight: 400; letter-spacing: 0.2px; }
  .troubleshooting { position: absolute; left: 150px; top: 645px; width: 940px; }
  .troubleshooting h2 {
    font-size: 20px; font-weight: 700; line-height: 32px;
    display: flex; align-items: center; gap: 10px;
  }
  .troubleshooting h2 svg { width: 32px; height: 32px; }
  .steps { list-style: none; margin-top: 21px; }
  .steps li {
    position: relative; padding-left: 31px;
    font-size: 14.5px; line-height: 24.5px; font-weight: 400;
    white-space: nowrap;
  }
  .steps li::before {
    content: ""; position: absolute; left: 11px; top: 7px;
    width: 10px; height: 10px; border-radius: 50%; background: var(--text);
  }
  .brand {
    position: absolute; left: 983px; top: 800px;
    font-weight: 700; font-size: 30px; line-height: 40px; letter-spacing: 1px;
  }
</style>
</head>
<body>
  <main class="splash">
    <svg class="status-icon" viewBox="0 0 100 92" aria-label="No Wi-Fi connection" role="img">
      <g fill="none" stroke="#fff" stroke-width="9" stroke-linecap="round">
        <path d="M8 34 Q50 2 92 34"/>
        <path d="M22 50 Q50 28 78 50"/>
        <path d="M36 65 Q50 54 64 65"/>
        <line x1="14" y1="6" x2="84" y2="86"/>
      </g>
      <circle cx="50" cy="80" r="6" fill="#fff"/>
    </svg>

    <h1 class="headline">Waiting for connection to<br>Wi-Fi access point...</h1>

    <svg class="cable" viewBox="0 0 1200 900" aria-hidden="true">
      <polyline points="463,535 1057,535 1057,512" fill="none" stroke="var(--cable)" stroke-width="4"/>
      <rect x="455" y="528" width="14" height="14" rx="2" fill="#444"/>
    </svg>

    <div class="device" role="img" aria-label="Tractor cab industrial computer showing the seeding application">
      <div class="device-screen"></div>
    </div>
    <div class="label label-computer">Tractor cab computer</div>
    <div class="label label-cable">Ethernet cable</div>

    <div class="access-point" role="img" aria-label="Outdoor Wi-Fi access point with two antennas"></div>
    <div class="label label-ap">Wi-Fi access point<span class="model">NETVALE AX300-OUTDOOR</span></div>

    <section class="troubleshooting">
      <h2>
        <svg viewBox="0 0 32 32" aria-hidden="true">
          <g fill="none" stroke="#fff" stroke-width="1.8" stroke-linecap="round" stroke-linejoin="round">
            <circle cx="16" cy="12" r="7"/>
            <circle cx="16" cy="12" r="3"/>
            <path d="M16 2v3M16 19v3M6 12h3M23 12h3M9 5l2 2M21 17l2 2M23 5l-2 2M11 17l-2 2"/>
            <path d="M4 29l8-5M28 29l-8-5"/>
          </g>
        </svg>
        Troubleshooting steps:
      </h2>
      <ul class="steps">
        <li>This screen should only be visible for a short time on boot.</li>
        <li>If this screen stays visible for more than a minute:</li>
        <li>Verify that the Wi-Fi Access Point (AP) powers up when this system does (indicated by a green light on the side of the AP).</li>
        <li>Check the Ethernet cable between this system and the AP for damage, and replace it if necessary.</li>
        <li>Power-cycle this system and wait for it to reboot fully.</li>
        <li>If the issue persists, contact KTWG support for further assistance.</li>
      </ul>
    </section>

    <div class="brand">KTWG</div>
  </main>
</body>
</html>
```